Webdesign für Honigmanufaktur
Zielgruppe
Imkerei, Verkauf von Honig und Honigerzeugnissen, so wie Bienenwachskerzen.
Zielgruppe sind vermutlich Frauen im mittleren bis gehobenen Alter.
Aufgabenstellung
Es gibt ein Firmenlogo.
Ich bevorzuge als Grundfarbe weiß, lasse mich aber von guten Einfällen gerne überraschen.
Die Website www.kelvaroni.at finde ich sehr ansprechend.
Nur ohne Musik.
Ohne Deutsch/Englisch Auswahl.
Es soll danach Word press verwendet werden.

```html
<!DOCTYPE html>
<html lang="de">
<head>
<meta charset="utf-8">
<title>Wabenhaus Waldtal – Der Shop</title>
<link rel="stylesheet" href="https://fonts.googleapis.com/css2?family=Roboto:wght@400;500;700&family=Roboto+Condensed:wght@400;700&family=Lato:wght@300;400&display=swap">
<style>
:root{
  --bg:#f1f1f1;
  --page:#ffffff;
  --honey:#f5a623;
  --brown:#5b3a1c;
  --ink:#2f2f2f;
  --muted:#8a8a8a;
  --line:#e6e6e6;
  --link:#2aa3d9;
  --tile:#ebebeb;
}
*{box-sizing:border-box;margin:0;padding:0}
html,body{width:683px;height:1200px;overflow:hidden;background:var(--bg)}
body{font-family:"Roboto",sans-serif;color:var(--ink);position:relative}
.page{position:absolute;left:32px;top:32px;width:619px;height:1133px;background:var(--page)}
.abs{position:absolute}

/* header */
.account{left:428px;top:4px;width:82px;border-bottom:1px solid var(--line);padding-bottom:3px;display:flex;gap:7px;font-family:"Roboto Condensed",sans-serif;font-size:3.6px;letter-spacing:.5px;color:var(--muted)}
.brand{left:244px;top:3px;width:130px;text-align:center}
.brand-dot{width:22px;height:22px;border-radius:50%;background:var(--honey);margin:0 auto 6px}
.brand-name{font-family:"Roboto Condensed",sans-serif;font-weight:700;color:var(--brown);font-size:6.6px;letter-spacing:.4px;line-height:7.5px}
.nav{top:37px;font-family:"Roboto Condensed",sans-serif;font-size:4.3px;letter-spacing:1px;color:#6a6a6a}
.nav.active{color:var(--honey)}
.nav.active::before,.nav.active::after{content:"";position:absolute;left:6px;right:6px;height:3px;border:1px solid var(--brown)}
.nav.active::before{top:-5px;border-bottom:none}
.nav.active::after{bottom:-5px;border-top:none}
.header-rule{left:0;top:52px;width:619px;border-top:1px solid var(--line)}

/* banner & filters */
.banner{left:113px;top:65px;width:387px;height:55px;background:linear-gradient(90deg,#4f5b3c 0%,#8b86b6 22%,#6b6396 45%,#4c5a38 60%,#8378b8 82%,#5b6b3e 100%)}
.filters{left:118px;top:126px;display:flex;gap:10px;font-size:4.6px;color:var(--ink)}
.filters span::after{content:"";display:inline-block;width:2px;height:2px;border-right:.7px solid var(--ink);border-bottom:.7px solid var(--ink);transform:rotate(45deg);margin:0 0 1px 3px}
.filter-rule{left:113px;top:138px;width:387px;border-top:1px solid var(--line)}

/* products */
.grid{left:118px;top:156px;display:grid;grid-template-columns:repeat(4,87px);column-gap:9.7px;grid-auto-rows:169.5px}
.card{position:relative;text-align:center}
.jar{width:87px;height:87px;background:var(--tile)}
.jar.vanille{background:radial-gradient(ellipse 30% 38% at 50% 50%,#f2d86a 0%,#f4e7a6 55%,var(--tile) 100%)}
.jar.orange{background:radial-gradient(ellipse 30% 38% at 50% 50%,#e69a1e 0%,#f0c36f 55%,var(--tile) 100%)}
.jar.karamell{background:radial-gradient(ellipse 30% 38% at 50% 50%,#b2581a 0%,#d99a64 55%,var(--tile) 100%)}
.card h3{position:absolute;top:94px;left:0;right:0;font-weight:400;font-size:4.6px}
.stars{position:absolute;top:112px;left:0;right:0;font-size:4.4px;letter-spacing:-.2px;color:#a5a5a5}
.price{position:absolute;top:120px;left:0;right:0;font-size:6px;color:var(--honey)}
.unit{position:absolute;top:130px;left:0;right:0;font-size:3.3px}
.tax{position:absolute;top:137px;left:0;right:0;font-size:3.3px}
.tax a{color:var(--link);text-decoration:none}
.cart{position:absolute;top:148px;left:15px;width:58px;height:11px;border:1px solid var(--honey);font-size:3.7px;font-style:italic;line-height:9px;color:var(--ink)}

/* newsletter */
.newsletter{left:118px;top:690px;width:387px;height:96px;background:linear-gradient(90deg,#f3f3f3 0%,#f6f6f6 40%,#e2e2e2 75%,#ededed 100%)}
.newsletter h2{position:absolute;top:29px;left:0;right:0;text-align:center;font-family:"Lato",sans-serif;font-weight:300;font-size:9px;letter-spacing:.6px;color:var(--ink)}
.nl-input{position:absolute;left:105px;top:49px;width:110px;height:14px;background:#fff;border:1px solid #dcdcdc;font-size:3.8px;color:var(--muted);line-height:12px;padding-left:6px}
.nl-button{position:absolute;left:217px;top:49px;width:58px;height:14px;background:var(--honey);color:#fff;font-size:3.8px;letter-spacing:.8px;text-align:center;line-height:14px}

/* about text */
.about-title{left:0;top:808px;width:619px;text-align:center;font-family:"Lato",sans-serif;font-weight:300;font-size:9.4px;letter-spacing:1px}
.about{left:150px;top:838px;width:320px;font-size:3.9px;line-height:7px;color:var(--muted)}
.about strong{display:block;color:var(--ink);font-weight:500}
.about p{margin-bottom:7px}

/* footer */
.footer-rule{left:113px;top:959px;width:387px;border-top:1px solid var(--honey)}
.fcol{top:973px;width:90px;font-size:3.9px;line-height:7.7px;color:var(--muted)}
.fcol h4{font-size:4.2px;font-weight:500;color:var(--ink);margin-bottom:6px}
.fcol b{color:var(--ink);font-weight:500}
.social{left:118px;top:1059px;display:flex;gap:7px}
.social i{display:block;width:4px;height:4px;border-radius:50%;background:#555}
.bottom-rule{left:0;top:1081px;width:619px;border-top:1px solid var(--line)}
.copyright{left:0;top:1094px;width:619px;text-align:center;font-size:3.7px;color:var(--muted)}
.payments{left:255px;top:1107px;display:flex;gap:4.5px}
.payments span{width:17px;height:11px;border:1px solid #dedede;font-size:3.2px;font-weight:500;color:#555;text-align:center;line-height:9px}
</style>
</head>
<body>
<div class="page">
  <header>
    <div class="abs account"><span>MEIN KONTO</span><span>WARENKORB (0)</span></div>
    <span class="abs nav" style="left:133px">STARTSEITE</span>
    <span class="abs nav" style="left:179px">DIE MANUFAKTUR</span>
    <span class="abs nav" style="left:237px">DER HONIG</span>
    <div class="abs brand">
      <div class="brand-dot"></div>
      <div class="brand-name">WABENHAUS<br>WALDTAL</div>
    </div>
    <span class="abs nav" style="left:353px">DAS BIENENWACHS</span>
    <span class="abs nav active" style="left:419px">DER SHOP</span>
    <span class="abs nav" style="left:465px">KONTAKT</span>
    <div class="abs header-rule"></div>
  </header>

  <div class="abs banner" role="img" aria-label="Foto: Biene auf blühendem Lavendel"></div>
  <div class="abs filters"><span>PREIS AUFSTEIGEND</span><span>HONIG IM GLAS</span><span>ANZEIGEN: 20</span></div>
  <div class="abs filter-rule"></div>

  <main class="abs grid">
    <div class="card"><div class="jar vanille" role="img" aria-label="Produktfoto: Honigglas Vanille"></div><h3>Honig mit Vanille</h3><div class="stars">★★★★★</div><div class="price">€5,95</div><div class="unit">Grundpreis: €5,95 /100g</div><div class="tax">Inkl. Mwst.; zzgl. <a href="#">Versandkosten</a></div><div class="cart">In den Warenkorb legen</div></div>
    <div class="card"><div class="jar orange" role="img" aria-label="Produktfoto: Honigglas Orange"></div><h3>Honig mit Orange</h3><div class="stars">★★★★★</div><div class="price">€5,95</div><div class="unit">Grundpreis: €5,95 /100g</div><div class="tax">Inkl. Mwst.; zzgl. <a href="#">Versandkosten</a></div><div class="cart">In den Warenkorb legen</div></div>
    <div class="card"><div class="jar karamell" role="img" aria-label="Produktfoto: Honigglas Karamell"></div><h3>Honig mit Karamell</h3><div class="stars">★★★★★</div><div class="price">€5,95</div><div class="unit">Grundpreis: €5,95 /100g</div><div class="tax">Inkl. Mwst.; zzgl. <a href="#">Versandkosten</a></div><div class="cart">In den Warenkorb legen</div></div>
    <div class="card"><div class="jar vanille" role="img" aria-label="Produktfoto: Honigglas Vanille"></div><h3>Honig mit Vanille</h3><div class="stars">★★★★★</div><div class="price">€5,95</div><div class="unit">Grundpreis: €5,95 /100g</div><div class="tax">Inkl. Mwst.; zzgl. <a href="#">Versandkosten</a></div><div class="cart">In den Warenkorb legen</div></div>

    <div class="card"><div class="jar karamell" role="img" aria-label="Produktfoto: Honigglas Karamell"></div><h3>Honig mit Karamell</h3><div class="stars">★★★★★</div><div class="price">€5,95</div><div class="unit">Grundpreis: €5,95 /100g</div><div class="tax">Inkl. Mwst.; zzgl. <a href="#">Versandkosten</a></div><div class="cart">In den Warenkorb legen</div></div>
    <div class="card"><div class="jar vanille" role="img" aria-label="Produktfoto: Honigglas Vanille"></div><h3>Honig mit Vanille</h3><div class="stars">★★★★★</div><div class="price">€5,95</div><div class="unit">Grundpreis: €5,95 /100g</div><div class="tax">Inkl. Mwst.; zzgl. <a href="#">Versandkosten</a></div><div class="cart">In den Warenkorb legen</div></div>
    <div class="card"><div class="jar orange" role="img" aria-label="Produktfoto: Honigglas Orange"></div><h3>Honig mit Orange</h3><div class="stars">★★★★★</div><div class="price">€5,95</div><div class="unit">Grundpreis: €5,95 /100g</div><div class="tax">Inkl. Mwst.; zzgl. <a href="#">Versandkosten</a></div><div class="cart">In den Warenkorb legen</div></div>
    <div class="card"><div class="jar vanille" role="img" aria-label="Produktfoto: Honigglas Vanille"></div><h3>Honig mit Vanille</h3><div class="stars">★★★★★</div><div class="price">€5,95</div><div class="unit">Grundpreis: €5,95 /100g</div><div class="tax">Inkl. Mwst.; zzgl. <a href="#">Versandkosten</a></div><div class="cart">In den Warenkorb legen</div></div>

    <div class="card"><div class="jar vanille" role="img" aria-label="Produktfoto: Honigglas Vanille"></div><h3>Honig mit Vanille</h3><div class="stars">★★★★★</div><div class="price">€5,95</div><div class="unit">Grundpreis: €5,95 /100g</div><div class="tax">Inkl. Mwst.; zzgl. <a href="#">Versandkosten</a></div><div class="cart">In den Warenkorb legen</div></div>
    <div class="card"><div class="jar orange" role="img" aria-label="Produktfoto: Honigglas Orange"></div><h3>Honig mit Orange</h3><div class="stars">★★★★★</div><div class="price">€5,95</div><div class="unit">Grundpreis: €5,95 /100g</div><div class="tax">Inkl. Mwst.; zzgl. <a href="#">Versandkosten</a></div><div class="cart">In den Warenkorb legen</div></div>
    <div class="card"><div class="jar vanille" role="img" aria-label="Produktfoto: Honigglas Vanille"></div><h3>Honig mit Vanille</h3><div class="stars">★★★★★</div><div class="price">€5,95</div><div class="unit">Grundpreis: €5,95 /100g</div><div class="tax">Inkl. Mwst.; zzgl. <a href="#">Versandkosten</a></div><div class="cart">In den Warenkorb legen</div></div>
    <div class="card"><div class="jar karamell" role="img" aria-label="Produktfoto: Honigglas Karamell"></div><h3>Honig mit Karamell</h3><div class="stars">★★★★★</div><div class="price">€5,95</div><div class="unit">Grundpreis: €5,95 /100g</div><div class="tax">Inkl. Mwst.; zzgl. <a href="#">Versandkosten</a></div><div class="cart">In den Warenkorb legen</div></div>
  </main>

  <section class="abs newsletter" role="img" aria-label="Hintergrundfoto: Bienen, hell ausgeblendet">
    <h2>JETZT FÜR UNSEREN AKTUELLEN NEWSLETTER ANMELDEN</h2>
    <div class="nl-input">E-Mail Adresse hier eingeben ...</div>
    <div class="nl-button">ABSENDEN</div>
  </section>

  <h2 class="abs about-title">EXKLUSIVER HONIG AUS DEM PFÄLZERWALD</h2>
  <section class="abs about">
    <p><strong>Lorem ipsum dolor sit amet, consetetur sadipscing elitr, sed diam nonumy eirmod tempor invidunt</strong>Lorem ipsum dolor sit amet, consetetur sadipscing elitr, sed diam nonumy eirmod tempor invidunt ut labore et dolore magna aliquyam erat, sed diam voluptua. At vero eos et accusam et justo duo dolores et ea rebum. Stet clita kasd gubergren, no sea takimata sanctus est Lorem ipsum dolor sit amet. Lorem ipsum dolor sit amet, consetetur sadipscing elitr, sed diam nonumy eirmod tempor invidunt ut labore et dolore magna aliquyam erat, sed diam voluptua. At vero eos et accusam et justo duo dolores et ea rebum. Stet clita kasd gubergren, no sea takimata sanctus est Lorem ipsum dolor sit amet, consetetur sadipscing elitr, sed diam nonumy eirmod tempor invidunt ut labore.</p>
    <p><strong>Lorem ipsum dolor sit amet, consetetur sadipscing elitr, sed diam nonumy eirmod tempor invidunt</strong>Lorem ipsum dolor sit amet, consetetur sadipscing elitr, sed diam nonumy eirmod tempor invidunt ut labore et dolore magna aliquyam erat, sed diam voluptua. At vero eos et accusam et justo duo dolores et ea rebum. Stet clita kasd gubergren, no sea takimata sanctus est Lorem ipsum dolor sit amet. Lorem ipsum dolor sit amet, consetetur sadipscing elitr, sed diam nonumy eirmod tempor invidunt ut labore et dolore magna aliquyam erat, sed diam voluptua. At vero eos et accusam et justo duo dolores et ea rebum. Stet clita kasd gubergren, no sea takimata sanctus est Lorem ipsum dolor sit amet. Lorem ipsum dolor sit amet, consetetur sadipscing elitr, sed diam nonumy eirmod tempor invidunt ut labore et</p>
  </section>

  <footer>
    <div class="abs footer-rule"></div>
    <div class="abs fcol" style="left:118px;width:90px">
      <h4>Wabenhaus © 2018</h4>
      Lorem ipsum dolor sit amet, consetetur sadipscing elitr, sed diam nonumy eirmod tempor invidunt ut labore et dolore magna aliquyam erat, sed diam voluptua. Lorem ipsum dolor sit amet, consetetur sadipscing<br><br>
      <b>Telefon:</b> 0000 000 0000<br>
      <b>E-Mail:</b> service@wabenhaus-waldtal.de
    </div>
    <div class="abs fcol" style="left:215px"><h4>Unternehmen</h4>Die Manufaktur<br>Der Honig<br>Das Bienenwachs<br>Kontaktformular<br>Datenschutz<br>Impressum</div>
    <div class="abs fcol" style="left:312px"><h4>Service</h4>FAQ<br>Lieferung &amp; Versand<br>AGB<br>Widerrufsbelehrung<br>Widerrufsformular<br>Glossar<br>Kundenmeinungen</div>
    <div class="abs fcol" style="left:408px"><h4>Mein Konto</h4>Kundenkonto anlegen<br>Meine Bestellungen<br>Meine Nachrichten<br>Mein Wunschzettel<br>Produkte vergleichen</div>
    <div class="abs social" aria-label="Soziale Netzwerke"><i></i><i></i><i></i><i></i><i></i></div>
    <div class="abs bottom-rule"></div>
    <div class="abs copyright">Copyright © 2018 Wabenhaus Waldtal | Musterstraße 10 | 12345 Musterstadt | Tel. 012 345 678 | Fax 012 345 678 | info@wabenhaus-waldtal.de</div>
    <div class="abs payments"><span>Vexa</span><span>Paynd</span><span>Mondo</span><span>Dicora</span><span>Amvio</span></div>
  </footer>
</div>
</body>
</html>
```